Software allocation system needs a business card design

We need a business card designed for our software platform - www.tallivo.com.au

At the moment the logo and website is all black and white, we are happy for suggestions on implementing some colour throughout either the logo or business card.

Industry/Entity Type

Software

Font styles to use
Sans Serif

Colors

Designer to choose colors to be used in the design.

```html
<!DOCTYPE html>
<html lang="en">
<head>
<meta charset="utf-8">
<title>Tallivo Business Card</title>
<link rel="stylesheet" href="https://fonts.googleapis.com/css2?family=Arimo:wght@400;700&display=swap">
<style>
  :root {
    --ink: #111111;
    --paper: #ffffff;
    --band-dark: #2b2b2b;
    --band-mid: #8a8a85;
    --band-light: #e6e6e2;
  }
  html, body {
    margin: 0;
    padding: 0;
    overflow: hidden;
    background: var(--paper);
  }
  .card {
    position: relative;
    width: 1200px;
    height: 655px;
    background: var(--paper);
    overflow: hidden;
    font-family: "Arimo", Arial, sans-serif;
    color: var(--ink);
  }
  .brand {
    position: absolute;
    left: 60px;
    top: 42px;
    display: flex;
    align-items: center;
    gap: 22px;
  }
  .brand-dot {
    width: 78px;
    height: 78px;
    border-radius: 50%;
    background: var(--ink);
  }
  .brand-name {
    font-size: 128px;
    font-weight: 400;
    letter-spacing: 10px;
    line-height: 1;
  }
  .tagline {
    position: absolute;
    left: 33px;
    top: 185px;
    margin: 0;
    font-size: 33px;
    font-weight: 400;
    letter-spacing: 0.2px;
    white-space: nowrap;
  }
  .contacts {
    position: absolute;
    left: 33px;
    top: 318px;
    margin: 0;
    font-size: 37px;
    line-height: 53px;
  }
  .contacts dt {
    display: inline;
    font-weight: 700;
  }
  .contacts dd {
    display: inline;
    margin: 0;
  }
  .contact-row { display: block; white-space: nowrap; }
  .postal {
    position: absolute;
    left: 597px;
    top: 527px;
    transform: translateX(-50%);
    margin: 0;
    font-style: normal;
    font-size: 32px;
    line-height: 53px;
    text-align: center;
    white-space: nowrap;
  }
  .edge-rule {
    position: absolute;
    left: 1155px;
    top: 37px;
    width: 13px;
    height: 583px;
    background: var(--ink);
  }
  .base-band {
    position: absolute;
    left: 0;
    bottom: 0;
    width: 100%;
    height: 24px;
    background: linear-gradient(90deg, var(--band-dark) 0%, var(--band-mid) 40%, var(--band-light) 100%);
  }
</style>
</head>
<body>
  <div class="card">
    <div class="brand">
      <span class="brand-dot"></span>
      <span class="brand-name">TALLIVO</span>
    </div>
    <p class="tagline">PLANNING AND COMPLIANCE FOR HEAVY INDUSTRY</p>
    <dl class="contacts">
      <span class="contact-row"><dt>Mobile:</dt> <dd>1727272727</dd></span>
      <span class="contact-row"><dt>Email:</dt> <dd>hello.team@tallivo.com.au</dd></span>
      <span class="contact-row"><dt>Website:</dt><dd>www.tallivo.com.au</dd></span>
    </dl>
    <address class="postal">P.O Box 318<br>Hillcrest 1540</address>
    <div class="edge-rule"></div>
    <div class="base-band"></div>
  </div>
</body>
</html>
```